Web Design job: SaaS start-up needs a cutting-edge web design

What's Needed:
- All designs files created
- Fully coded implementation in HTML/CSS/Bootstrap
- Pages: 5 -- see content here http://www.TeamVerdexa.com
-- Home Page
-- The Hidden Value
-- Benefits
-- About us
-- Careers
- The existing site has the textual content for each page. We can tweak to meet specific designs if needed.
- You will need to update/create image and interactive content for pages.

Reference:
Our existing website has a lot of content on it for reference -
http://www.TeamVerdexa.com

Description:
We need a web design that focuses in the UX and conveys the idea of magically fixing company problems by way of using our software.

Home Page
The main goal is to Drive Sales of the SaaS tool. When a visitor lands on our home page they should see: What we do, How we can help their problem and How to contact us.
1. Quickly understand What We Do
-- we sell SaaS software.
-- Need to quickly convey what our software does. It's seems complicated but really its not. See the description in about us for more info and visit our existing site.

2. How we can help their problem
-- We aim to solve any problem related to employees
-- Even if the visitor does not have a specific problem in mind, there are several areas organizations can always improve: (some examples below)
---- Create Stronger, More Productive Teams
---- Build Better Communications Pathways
---- Encourage Innovation and Positive Change
---- Develop and Retain Strong "Company Culture"

3. Be able to Contact Us to get started
-- contacting us to get a sales lead is the ultimate goal.
-- the user should not have to hunt to contact us. needs to be easy.

Other Pages (Hidden Value, Benefit, About Us, Careers):
-- These are informative pages about our software and process.
-- If we grab the attention of the user on the home page then these are the pages that they will explore for more info.
-- Should be able to link to these pages from the main nav or from sections with the homepage. For example: What We Do sections could link to the benefits page. How we help their problem sections could link to the Hidden Value page. Regardless of what links to where, the idea is that we will be able to nav to other areas.

About Us:
Our company name is TeamVerdexa (as in Organizational Analysis). We provide a software as a service (SaaS) that uses a simple 6-question survey to analyze the relationships of people within an Organization and provide leaders with ground-breaking Insights about their teams, interactive social network data visualizations to explore their team's composition and we give detailed profiles of the key players (i.e, who are the Social Bridges, Who are the Knowledge Bottlenecks, Who are the Best Mentors, Who are the people that are completely disconnected/out of the loop). Leaders then use this information to make high level organizational decisions.

What's unique about our software:
-- Powerful analysis results from just a 6-question "pulse-surveys"
-- Innovative Tools for visually exploring the organization through relationships as opposed to org-chart
-- Get real-time results as opposed to waiting months with traditional methods
-- Traditional Org-charts represent the organization's skeleton, whereas we uncover the organization's neural network (how it solves problems).

Preferred fonts (but could be convinced otherwise if looks great):
-- Section titles - Aleo
-- Main body - Lato
-- TeamVerdexa logo - Philosopher

Things we like:
-- We like a big slider as the top of the landing page.

Colors to include:
-- Colors in the logo (red, blue, green, teal) as accent colors

Feel of the site:
-- Cutting-edge Software
-- Professional
-- Social Network flare (we analyze relationships)

Note:
If we find a great match with a designer there is strong possibility to continue the relationship with follow on work redesigning our web-based application.

Target Market(s)

Current customers are Morrow Pike & Fenwell, Clearbrook Valley Bank.
We target anyone that manages a large team. Such as Corporate Leaders, High Level Managers, HR Leaders

Industry/Entity Type

Business Software

Contact Information for Business Card

Logo image
Name of company "TEAMVERDEXA" In Philosopher font.
Tagline: "Unlock the Hidden Value In Your Teams"
Person's Name, Title, email, phone.

Coding

Coded - Design and coding required

Number of Pages Required

4 page

Font styles to use
Other font styles liked:
• Lato, Philosopher, Aero

Colors
ec1f27
0255a3

Requirements
Must have
• See description.
Nice to have
• Things we like:
• We like a big slider as the top of the landing page. Ours is a little clunky and outdated but something fresh and sleek would be great.
• Colors to include:
• We would like to use the colors in the logo as accent colors in the site to give a consistent look and feel.
• Feel of the site:
• Cutting-edge Software
• Professional
• Social Network flare (we analyze relationships)

```html
<!DOCTYPE html>
<html lang="en">
<head>
<meta charset="utf-8">
<title>TeamVerdexa – Home</title>
<link href="https://fonts.googleapis.com/css2?family=Aleo:wght@400;700&family=Lato:wght@400;700&family=Philosopher:wght@400;700&display=swap" rel="stylesheet">
<style>
:root{
  --red:#ec1f27;
  --blue:#0255a3;
  --navy:#1f2a5a;
  --ink:#222;
  --body:#444;
  --hero-bg:#f1f0ed;
  --line:#d8d8d8;
  --white:#fff;
}
*{margin:0;padding:0;box-sizing:border-box}
html,body{width:1200px;height:2635px;overflow:hidden;background:var(--white)}
body{position:relative;font-family:'Lato',sans-serif;color:var(--body)}
.abs{position:absolute}
.title{font-family:'Aleo',serif;font-weight:400;color:var(--ink);font-size:28px;text-align:center;width:1200px;left:0}
.lead{font-size:12.5px;line-height:21px;text-align:center;width:640px;left:280px;color:var(--ink)}
.btn{position:absolute;border:1px solid #333;border-radius:18px;font-size:11.5px;color:var(--ink);display:flex;align-items:center;justify-content:center;background:transparent}

/* header */
.site-header{position:absolute;left:0;top:0;width:1200px;height:132px;background:var(--white);box-shadow:0 2px 6px rgba(0,0,0,.08);z-index:2}
.brand{left:162px;top:52px;font-family:'Philosopher',sans-serif;font-weight:700;font-size:22px;color:var(--navy);letter-spacing:.5px;display:flex;align-items:center;gap:10px}
.brand-dot{width:14px;height:14px;border-radius:50%;background:var(--red)}
.phone{left:773px;top:26px;font-size:19px;color:var(--red);display:flex;align-items:center;gap:7px}
.socials{left:945px;top:25px;display:flex;gap:6px}
.socials span{width:25px;height:25px;border:1px solid #bbb;border-radius:50%}
.main-nav{top:82px;font-size:14px;color:var(--ink)}
.nav-swoosh{left:472px;top:94px}

/* hero */
.hero{left:0;top:132px;width:1200px;height:527px;background:var(--hero-bg)}
.hero-title{left:162px;top:155px;font-family:'Aleo',serif;font-size:34px;color:var(--ink);letter-spacing:1px}
.hero-text{left:162px;top:214px;width:380px;font-size:18.5px;line-height:29px;color:#222}
.hero .btn{left:162px;top:325px;width:145px;height:32px;font-weight:700;font-size:11px}
.dots{left:162px;top:415px;display:flex;gap:3px}
.dots span{width:15px;height:15px;border-radius:50%;background:#aaa}
.dots span:first-child{background:var(--red)}
.network-art{left:610px;top:30px;width:470px;height:450px;border-radius:50%;background:radial-gradient(circle at 50% 45%,rgba(200,40,120,.35),rgba(90,70,200,.22) 45%,rgba(60,170,80,.10) 70%,rgba(241,240,237,0) 75%)}

/* what we do */
.service{position:absolute;top:808px;width:230px;text-align:center}
.service svg{display:block;margin:0 auto}
.service h3{font-family:'Aleo',serif;font-weight:400;font-size:13.5px;color:var(--ink);margin-top:22px}
.service p{font-size:11.5px;line-height:20px;margin-top:11px;color:#444}
.service .btn{position:relative;margin:28px auto 0;width:100px;height:32px}

/* about */
.about{left:0;top:1112px;width:615px;height:434px;background:var(--blue);color:var(--white)}
.about h2{position:absolute;left:167px;top:58px;font-family:'Aleo',serif;font-weight:400;font-size:27px}
.about p{position:absolute;left:162px;top:110px;width:410px;font-size:11.8px;line-height:22px}
.about .btn{left:162px;top:340px;width:100px;height:32px;border-color:var(--white);color:var(--white)}
.about-photo{left:615px;top:1112px;width:585px;height:434px;background:linear-gradient(135deg,#1b3150,#0c1526 55%,#3a3430)}

/* help */
.help-art{left:228px;top:1731px;width:348px;height:196px;background:linear-gradient(#f3f4f7,#dde2ea);border:10px solid #3b3b3b;border-bottom-width:14px;border-radius:6px}
.help-list{left:607px;top:1722px;width:400px;list-style:none;font-size:13.2px;color:var(--ink);line-height:21px}
.help-list li{display:flex;gap:12px;margin-bottom:9px}
.help-list svg{flex:none;margin-top:4px}
.divider{left:0;top:2000px;width:1200px;height:1px;background:var(--line)}

/* contact */
.map{left:0;top:2154px;width:756px;height:350px;background:linear-gradient(135deg,#ecebe5,#e2e6d9 60%,#e8e3cf)}
.contact-panel{left:756px;top:2154px;width:444px;height:350px;border:3px solid #000;background:var(--white)}
.contact-panel h3{position:absolute;left:26px;top:22px;font-family:'Aleo',serif;font-weight:400;font-size:18px;color:var(--ink)}
.field{position:absolute;border:1px solid #ccc;font-size:9px;color:#333;padding:7px 6px}
.submit{position:absolute;left:26px;top:175px;width:88px;height:26px;border-radius:13px;background:var(--red);color:var(--white);font-size:11px;display:flex;align-items:center;justify-content:center}
.contact-panel h4{position:absolute;left:26px;top:236px;font-family:'Aleo',serif;font-weight:400;font-size:18px;color:var(--ink)}
.addr{position:absolute;top:268px;font-size:10.5px;line-height:19px;color:#222}

/* footer */
.footer-nav{top:2533px;font-size:14px;color:var(--ink)}
.footer-line{left:162px;top:2570px;width:875px;height:1px;background:var(--line)}
.copyright{left:0;width:1200px;top:2586px;text-align:center;font-size:11px;color:#222}
</style>
</head>
<body>

<header class="site-header">
  <div class="abs brand"><span class="brand-dot"></span>TEAM VERDEXA</div>
  <div class="abs phone">
    <svg width="16" height="16" viewBox="0 0 24 24"><path fill="#ec1f27" d="M6.6 10.8c1.4 2.8 3.8 5.1 6.6 6.6l2.2-2.2c.3-.3.7-.4 1-.2 1.1.4 2.3.6 3.6.6.6 0 1 .4 1 1V20c0 .6-.4 1-1 1C10.6 21 3 13.4 3 4c0-.6.4-1 1-1h3.5c.6 0 1 .4 1 1 0 1.3.2 2.5.6 3.6.1.3 0 .7-.2 1z"/></svg>
    (480) 555-0142
  </div>
  <div class="abs socials"><span></span><span></span><span></span></div>
  <nav>
    <span class="abs main-nav" style="left:476px">Home</span>
    <span class="abs main-nav" style="left:553px">What We Do</span>
    <span class="abs main-nav" style="left:675px">How We Can Help Their Problem</span>
    <span class="abs main-nav" style="left:924px">How to Contact Us</span>
  </nav>
  <svg class="abs nav-swoosh" width="46" height="22" viewBox="0 0 46 22"><path d="M2 8 Q20 26 44 2" stroke="#2b3a8c" stroke-width="3" fill="none" stroke-linecap="round"/></svg>
</header>

<section class="abs hero">
  <h1 class="abs hero-title">TEAM VERDEXA</h1>
  <p class="abs hero-text">Lorem ipsum dolor sit amet, consectetur adipi scing elit, sed do eiusmod tempor incididunt labore et dolore magnaal.</p>
  <span class="btn">READ MORE HERE</span>
  <div class="abs dots"><span></span><span></span><span></span><span></span></div>
  <div class="abs network-art" role="img" aria-label="Colourful social network graph of connected nodes"></div>
</section>

<section>
  <h2 class="abs title" style="top:693px">What We Do</h2>
  <p class="abs lead" style="top:742px">Lorem ipsum dolor sit amet, consectetur adipiscing elit, seLorem ipsum dolor sit amet, consectetur adipiscing elit, sed do eiusmod tempor incididunt ut labore et dolore magna alLorem ipsum dolor sit amet, consectetur adipiscing elit.</p>

  <div class="service" style="left:143px">
    <svg width="90" height="97" viewBox="0 0 90 97"><rect x="10" y="50" width="70" height="40" rx="4" fill="#ec1f27"/><rect x="2" y="88" width="86" height="7" rx="2" fill="#ec1f27"/><rect x="40" y="64" width="10" height="10" rx="5" fill="#fff"/></svg>
    <h3>On Line Pulse Survey</h3>
    <p>Lorem ipsum dolor sit ameloret, cecur adipiscing elit, seLorem ipsum.</p>
    <span class="btn">Read More</span>
  </div>
  <div class="service" style="left:372px">
    <svg width="110" height="97" viewBox="0 0 110 97" fill="none" stroke="#ec1f27" stroke-width="4"><path d="M20 35 L55 8 L95 25 L85 75 L40 88 L10 60 Z M20 35 L55 50 L95 25 M55 50 L85 75 M55 50 L40 88 M55 8 L55 50 M10 60 L55 50"/><g fill="#ec1f27"><circle cx="20" cy="35" r="6"/><circle cx="55" cy="8" r="6"/><circle cx="95" cy="25" r="6"/><circle cx="85" cy="75" r="6"/><circle cx="40" cy="88" r="6"/><circle cx="10" cy="60" r="6"/><circle cx="55" cy="50" r="6"/></g></svg>
    <h3>Proprietary Algorithm</h3>
    <p>Lorem ipsum dolor sit ameloret, cecur adipiscing elit, seLorem ipsum.</p>
    <span class="btn">Read More</span>
  </div>
  <div class="service" style="left:600px">
    <svg width="110" height="97" viewBox="0 0 110 97"><rect x="3" y="5" width="104" height="70" rx="3" fill="#ec1f27"/><rect x="10" y="12" width="90" height="56" fill="#fff"/><path d="M18 58 L35 38 L48 48 L68 24 L90 36" stroke="#ec1f27" stroke-width="4" fill="none"/><g fill="#ec1f27"><rect x="25" y="48" width="6" height="16"/><rect x="43" y="52" width="6" height="12"/><rect x="61" y="42" width="6" height="22"/><rect x="79" y="46" width="6" height="18"/><rect x="45" y="75" width="20" height="12"/><rect x="30" y="86" width="50" height="6"/></g></svg>
    <h3>Organizational Key Insights</h3>
    <p>Lorem ipsum dolor sit ameloret, cecur adipiscing elit, seLorem ipsum.</p>
    <span class="btn">Read More</span>
  </div>
  <div class="service" style="left:828px">
    <svg width="90" height="97" viewBox="0 0 90 97"><rect x="8" y="5" width="62" height="85" rx="3" fill="none" stroke="#ec1f27" stroke-width="7"/><g fill="#ec1f27"><rect x="20" y="22" width="38" height="6"/><rect x="20" y="36" width="38" height="6"/><rect x="20" y="50" width="25" height="6"/><path d="M48 80 L82 30 L90 36 L56 86 L46 90 Z"/></g></svg>
    <h3>Expert Review &amp; Action Plans</h3>
    <p>Lorem ipsum dolor sit ameloret, cecur adipiscing elit, seLorem ipsum.</p>
    <span class="btn">Read More</span>
  </div>
</section>

<section class="abs about">
  <h2>About Us</h2>
  <p>Our company name is TeamVerdexa (as in Organizational Analysis). We provide a softwareas a service that uses a simple 6-question survey to analyze the relationships of people within an Organization and provide leaders with ground -breaking Insights about their teams, interactive social network data visualizations to explore their team's composition and we give detailed profiles of the key players (i.e, who are the Social Bridges, Who are the Knowledge Bottlenecks, Who are the Best Mentors, Who are the people that are completely disconnected/out of the loop). Leaders then use this information to make high level organizational decisions.</p>
  <span class="btn">Read More</span>
</section>
<div class="abs about-photo" role="img" aria-label="Photo of hands at a laptop with a glowing digital network overlay"></div>

<section>
  <h2 class="abs title" style="top:1595px">How we can help their problem</h2>
  <p class="abs lead" style="top:1647px">Lorem ipsum dolor sit amet, consectetur adipiscing elit, seLorem ipsum dolor sit amet, consectetur adipiscing elit, sed do eiusmod tempor incididunt ut labore et dolore magna alLorem ipsum dolor sit amet, consectetur adipiscing elit.</p>
  <div class="abs help-art" role="img" aria-label="Line illustration of a laptop showing a person working with charts and devices"></div>
  <div class="abs" style="left:228px;top:1923px;width:348px;height:8px;background:#d6d6d6;border-radius:0 0 6px 6px"></div>
  <ul class="abs help-list">
    <li><svg width="12" height="12" viewBox="0 0 12 12"><circle cx="6" cy="3" r="2.5" fill="#ec1f27"/><circle cx="3" cy="8" r="2.5" fill="#0255a3"/><circle cx="9" cy="8" r="2.5" fill="#3aa64a"/></svg><span>We aim to solve any problem related to employees</span></li>
    <li><svg width="12" height="12" viewBox="0 0 12 12"><circle cx="6" cy="3" r="2.5" fill="#ec1f27"/><circle cx="3" cy="8" r="2.5" fill="#0255a3"/><circle cx="9" cy="8" r="2.5" fill="#3aa64a"/></svg><span>Even if the visitor does not have a specific problem in mind, there are several areas organizations can always improve</span></li>
    <li><svg width="12" height="12" viewBox="0 0 12 12"><circle cx="6" cy="3" r="2.5" fill="#ec1f27"/><circle cx="3" cy="8" r="2.5" fill="#0255a3"/><circle cx="9" cy="8" r="2.5" fill="#3aa64a"/></svg><span>Create Stronger, More Productive Teams</span></li>
    <li><svg width="12" height="12" viewBox="0 0 12 12"><circle cx="6" cy="3" r="2.5" fill="#ec1f27"/><circle cx="3" cy="8" r="2.5" fill="#0255a3"/><circle cx="9" cy="8" r="2.5" fill="#3aa64a"/></svg><span>Build Better Communications Pathways</span></li>
    <li><svg width="12" height="12" viewBox="0 0 12 12"><circle cx="6" cy="3" r="2.5" fill="#ec1f27"/><circle cx="3" cy="8" r="2.5" fill="#0255a3"/><circle cx="9" cy="8" r="2.5" fill="#3aa64a"/></svg><span>Encourage Innovation and Positive Change</span></li>
    <li><svg width="12" height="12" viewBox="0 0 12 12"><circle cx="6" cy="3" r="2.5" fill="#ec1f27"/><circle cx="3" cy="8" r="2.5" fill="#0255a3"/><circle cx="9" cy="8" r="2.5" fill="#3aa64a"/></svg><span>Develop and Retain Strong "Company Culture"</span></li>
  </ul>
</section>

<div class="abs divider"></div>

<section>
  <h2 class="abs title" style="top:2022px">How to Contact Us</h2>
  <p class="abs lead" style="top:2069px">Lorem ipsum dolor sit amet, consectetur adipiscing elit, seLorem ipsum dolor sit amet, consectetur adipiscing elit, sed do eiusmod tempor incididunt ut labore et dolore magna alLorem ipsum dolor sit amet, consectetur adipiscing elit.</p>
  <div class="abs map" role="img" aria-label="Street map showing the office location"></div>
  <div class="abs contact-panel">
    <h3>Contact Form</h3>
    <div class="field" style="left:26px;top:57px;width:190px;height:32px">Name:</div>
    <div class="field" style="left:26px;top:95px;width:190px;height:32px">Phone:</div>
    <div class="field" style="left:26px;top:133px;width:190px;height:32px">Email:</div>
    <div class="field" style="left:221px;top:57px;width:197px;height:108px">Message:</div>
    <span class="submit">SUBMIT</span>
    <h4>Address</h4>
    <div class="addr" style="left:26px">Harbour Point Offices<br>24, Quillon Yard, 3rd floor<br>London United Kingdom</div>
    <div class="addr" style="left:257px">Phone: +44 20 7946 0100<br>Fax: +44 20 7946 0101<br>E-mail: info@teamverdexa.com</div>
  </div>
</section>

<footer>
  <span class="abs footer-nav" style="left:322px">Home</span>
  <span class="abs footer-nav" style="left:392px">What We Do</span>
  <span class="abs footer-nav" style="left:506px">How We Can Help Their Problem</span>
  <span class="abs footer-nav" style="left:757px">How to Contact Us</span>
  <div class="abs footer-line"></div>
  <p class="abs copyright">© 2016 TeamVerdexa.All Copyrights are reserved. Term of Use. Privacy Policy</p>
</footer>

</body>
</html>
```